Design a building access mobile app for Quillo by Tamberlin Entry Systems

Hello, We're looking for an awesome designer to create an app design for our app Quillo, by Tamberlin Entry Systems. the mobile app allows employees open their office doors with their mobile phone. this means they don't have to use those plastic card badges or keys. We like clean modern design, dark and light themes. We don't have a logo yet.
Updates

Reason: Waiting on a couple designers to submit concepts

Target Market(s)

Commercial and employees

Industry/Entity Type

Building

Font styles to use
Sans Serif
Other font styles liked:
• Oswald extra light

Requirements
Must have
• nice clean design

```html
<!DOCTYPE html>
<html lang="en">
<head>
<meta charset="utf-8">
<title>Quillo — Register</title>
<link rel="stylesheet" href="https://fonts.googleapis.com/css2?family=Oswald:wght@200;300;400&family=Inter:wght@400;500&display=swap">
<style>
  :root {
    --backdrop: #1e93d0;
    --screen: #ffffff;
    --ink: #1c1c1c;
    --muted: #8a8f96;
    --rule: #e3e5e8;
    --brand: #2f5d92;
    --accent: #3a7fc8;
    --on-accent: #ffffff;
  }
  * { box-sizing: border-box; margin: 0; padding: 0; }
  html, body { width: 1200px; height: 864px; overflow: hidden; }
  body {
    background: var(--backdrop);
    font-family: "Oswald", sans-serif;
    position: relative;
  }
  .screen {
    position: absolute;
    left: 390px; top: 50px;
    width: 420px; height: 764px;
    background: var(--screen);
    box-shadow: 0 18px 40px rgba(0, 40, 80, 0.35);
  }
  .status-bar {
    position: relative;
    height: 28px;
    display: flex; align-items: center; justify-content: space-between;
    padding: 0 10px;
    font-family: "Inter", sans-serif;
    font-size: 12px; color: var(--ink);
  }
  .status-bar .left, .status-bar .right { display: flex; align-items: center; gap: 5px; }
  .status-bar .time {
    position: absolute; left: 50%; transform: translateX(-50%);
    font-weight: 500;
  }
  .brand {
    position: absolute; top: 150px; left: 0; right: 0;
    display: flex; justify-content: center; align-items: center; gap: 12px;
  }
  .brand-dot { width: 22px; height: 22px; border-radius: 50%; background: var(--brand); }
  .brand-name {
    font-weight: 400; font-size: 44px; color: var(--brand);
    letter-spacing: 1px;
  }
  .form { position: absolute; top: 330px; left: 52px; right: 52px; }
  .field {
    display: flex; align-items: flex-end; gap: 18px;
    height: 62px;
  }
  .field-icon { width: 24px; height: 24px; margin-bottom: 6px; flex: none; }
  .field-label {
    flex: 1;
    font-weight: 200; font-size: 17px; color: var(--muted);
    padding-bottom: 8px;
    border-bottom: 1px solid var(--rule);
  }
  .toggle {
    display: flex; align-items: center; gap: 10px;
    margin: 18px 0 0 42px;
    font-weight: 200; font-size: 12px; color: var(--muted);
  }
  .radio {
    width: 13px; height: 13px; border-radius: 50%;
    border: 1.5px solid var(--accent);
    display: flex; align-items: center; justify-content: center;
  }
  .radio::after { content: ""; width: 7px; height: 7px; border-radius: 50%; background: var(--accent); }
  .register {
    position: absolute; left: 42px; right: 42px; top: 600px;
    height: 60px; border-radius: 30px;
    background: var(--accent); color: var(--on-accent);
    display: flex; align-items: center; justify-content: center;
    font-weight: 300; font-size: 19px; letter-spacing: 1px;
  }
</style>
</head>
<body>
  <main class="screen">
    <header class="status-bar">
      <div class="left">
        <svg width="34" height="7" viewBox="0 0 34 7" aria-hidden="true">
          <circle cx="3.5" cy="3.5" r="3" fill="#1c1c1c"/><circle cx="10.5" cy="3.5" r="3" fill="#1c1c1c"/>
          <circle cx="17.5" cy="3.5" r="3" fill="#1c1c1c"/><circle cx="24.5" cy="3.5" r="2.5" fill="none" stroke="#1c1c1c"/>
          <circle cx="31" cy="3.5" r="2.5" fill="none" stroke="#1c1c1c"/>
        </svg>
        <span>Nettle</span>
        <svg width="14" height="10" viewBox="0 0 14 10" aria-hidden="true">
          <path d="M1 4a9 9 0 0 1 12 0M3 6a6 6 0 0 1 8 0M5 8a3 3 0 0 1 4 0" fill="none" stroke="#1c1c1c" stroke-width="1.4"/>
        </svg>
      </div>
      <span class="time">1:23 AM</span>
      <div class="right">
        <svg width="8" height="11" viewBox="0 0 8 11" aria-hidden="true">
          <path d="M1 3l6 5-3 2.5V.5L7 3 1 8" fill="none" stroke="#1c1c1c" stroke-width="1"/>
        </svg>
        <span>77%</span>
        <svg width="24" height="11" viewBox="0 0 24 11" aria-hidden="true">
          <rect x="0.5" y="0.5" width="20" height="10" rx="2" fill="none" stroke="#1c1c1c"/>
          <rect x="2" y="2" width="13" height="7" rx="1" fill="#1c1c1c"/>
          <rect x="21.5" y="3.5" width="2" height="4" rx="1" fill="#1c1c1c"/>
        </svg>
      </div>
    </header>

    <div class="brand">
      <span class="brand-dot"></span>
      <span class="brand-name">Quillo</span>
    </div>

    <form class="form">
      <label class="field">
        <svg class="field-icon" viewBox="0 0 24 24" aria-hidden="true">
          <rect x="2" y="6" width="20" height="13" fill="none" stroke="#6b7077" stroke-width="1.2"/>
          <path d="M2 6l10 7 10-7" fill="none" stroke="#6b7077" stroke-width="1.2"/>
        </svg>
        <span class="field-label">Email</span>
      </label>
      <label class="field">
        <svg class="field-icon" viewBox="0 0 24 24" aria-hidden="true">
          <rect x="4" y="11" width="16" height="11" fill="none" stroke="#6b7077" stroke-width="1.2"/>
          <path d="M8 11V7a4 4 0 0 1 8 0v4M12 15v3" fill="none" stroke="#6b7077" stroke-width="1.2"/>
        </svg>
        <span class="field-label">Password</span>
      </label>
      <label class="field">
        <svg class="field-icon" viewBox="0 0 24 24" aria-hidden="true">
          <rect x="4" y="11" width="16" height="11" fill="none" stroke="#6b7077" stroke-width="1.2"/>
          <path d="M8 11V7a4 4 0 0 1 8 0v4M12 15v3" fill="none" stroke="#6b7077" stroke-width="1.2"/>
        </svg>
        <span class="field-label">Confirm Password</span>
      </label>
      <div class="toggle"><span class="radio"></span><span>Enable Touch</span></div>
    </form>

    <div class="register">REGISTER</div>
  </main>
</body>
</html>
```